Toll Away Armed Harm

We need web design for an anti-gun violence campaign that will urge people to ring bells instead of shooting guns to bring in the New Year and whenever someone is killed by gun violence.
This campaign will raise funds for social agencies that help communities with social issues to help especially youth with no place to turn, play or dream. Also will fund New Gun Laws policies. Should be global in aspect but appealing to United States first.
Find poem by Lord Edmund Brackwell "Sing Larks, Swift Larks" as our theme on google.
This is a start up and nothing else to give. But need something eye catching for appeal of campaign.

Target Market(s)

Universal , more male oriented.

Industry/Entity Type

Gun

Number of Pages Required

1 page

Other font styles liked:
• Designers Can Choose

Requirements
Must have
• Strong imagery and vivid colors and bell of course.
Nice to have
• A stand out design beyond words that hit home. See attached file for website ideas

```html
<!DOCTYPE html>
<html lang="en">
<head>
<meta charset="utf-8">
<title>Toll Away Armed Harm</title>
<link rel="stylesheet" href="https://fonts.googleapis.com/css2?family=Roboto:wght@300;400&family=Roboto+Condensed:wght@300;400;700&family=Roboto+Slab:wght@300;400&family=Noto+Serif&display=swap">
<style>
:root{
  --brand-blue:#0a63b5;
  --logo-blue:#1d5f9f;
  --ink:#1e1e1e;
  --body:#4a4a4a;
  --light-bg:#ececec;
  --band-bg:#ededed;
  --orange:#f26a21;
  --footer:#3c3c3c;
  --white:#ffffff;
}
*{margin:0;padding:0;box-sizing:border-box}
html,body{width:924px;height:1200px;overflow:hidden;background:var(--white)}
body{position:relative;font-family:"Roboto",sans-serif;color:var(--ink)}
.abs{position:absolute}

.site-header{left:0;top:0;width:924px;height:62px;background:linear-gradient(#ffffff,#eef0f2)}
.logo{left:97px;top:20px;font-family:"Noto Serif",serif;font-size:17.5px;color:var(--logo-blue)}
.search{left:728px;top:14px;width:99px;height:25px;border:1px solid #b9bcc0;background:#fff;font-size:8px;color:#8a8a8a;padding:7px 0 0 7px;letter-spacing:.3px}
.search svg{position:absolute;right:5px;top:6px}

.main-nav{left:0;top:62px;width:924px;height:39px;background:var(--brand-blue)}
.nav-item{top:0;font-family:"Roboto Slab",serif;font-size:9px;color:#fff;letter-spacing:.4px;line-height:39px}
.nav-sep{top:8px;width:1px;height:24px;background:rgba(255,255,255,.3)}
.follow{left:732px;top:0;line-height:39px;font-size:8px;color:#fff;letter-spacing:.3px;display:flex;align-items:center;gap:7px}
.follow .dot{width:9px;height:9px;border-radius:50%;background:#fff}

.hero{left:98px;top:104px;width:728px;height:237px;background:linear-gradient(100deg,#4f7fc4 0%,#8aa3c4 30%,#a9a193 45%,#4f6b5c 60%,#5b86c9 75%,#b6aa96 90%);box-shadow:0 10px 12px -8px rgba(0,0,0,.35)}
.quote-box{left:0;top:68px;width:282px;height:124px;background:rgba(60,60,70,.55);padding:12px 18px}
.quote-box p{font-weight:300;font-size:15.5px;line-height:23px;color:#f2f2f2}
.quote-box hr{border:0;border-top:1px solid rgba(255,255,255,.45);margin:10px 0 9px}
.quote-box cite{font-style:italic;font-weight:300;font-size:11px;color:#fff}
.hero-dots{right:20px;bottom:13px;display:flex;gap:3px}
.hero-dots span{width:10px;height:10px;border-radius:50%;background:#fff}
.hero-dots span.on{background:#222;border:3px solid #fff}

.welcome h1{font-family:"Roboto Condensed",sans-serif;font-weight:400;font-size:16px;left:97px;top:354px}
.welcome p{left:97px;top:378px;width:404px;font-family:"Roboto Condensed",sans-serif;font-weight:300;font-size:10px;line-height:15.6px;color:#333}
.welcome-photo{left:579px;top:367px;width:247px;height:94px;background:linear-gradient(#7a4a55,#3a2d3a 60%,#6b4f60)}

.features{left:0;top:472px;width:924px;height:360px;background:var(--light-bg)}
.card{top:24px;width:222px;height:312px;background:#fff}
.card .photo{height:141px;background:linear-gradient(135deg,#6b6a70,#a04a4a 50%,#c9c7c3)}
.card h2{font-family:"Roboto Condensed",sans-serif;font-weight:400;font-size:13px;line-height:16px;margin:14px 18px 0}
.card p{font-weight:300;font-size:9.6px;line-height:15.6px;color:var(--body);margin:9px 30px 0 18px}
.read-more{font-family:"Roboto Condensed",sans-serif;font-size:10px;color:#222;display:flex;align-items:center;justify-content:space-between}
.card .read-more{margin:20px 18px 0 20px}

.blog h3{left:97px;top:845px;font-family:"Roboto Condensed",sans-serif;font-weight:400;font-size:13px}
.blog-dots{left:787px;top:847px;display:flex;gap:3px}
.blog-dots span{width:8px;height:8px;border-radius:50%;background:#c4c4c4}
.blog-dots span.on{background:var(--orange)}
.blog-photo{left:98px;top:871px;width:307px;height:156px;background:linear-gradient(180deg,#8f8f8a,#4a4c55 55%,#7c7a76)}
.blog-post{left:426px;top:875px;width:400px}
.blog-post h2{font-family:"Roboto Condensed",sans-serif;font-weight:400;font-size:12.5px}
.blog-post p{font-weight:300;font-size:9.2px;line-height:15.6px;color:var(--body);margin-top:7px}
.blog-post .read-more{justify-content:flex-start;gap:12px;margin-top:10px}

.donate-band{left:97px;top:1048px;width:729px;height:77px;background:var(--band-bg)}
.donate-band h2{left:27px;top:17px;font-family:"Roboto Condensed",sans-serif;font-weight:400;font-size:13px;line-height:16px}
.vline{top:14px;width:1px;height:48px;background:#c8c8c8}
.donate-band p{left:176px;top:16px;width:225px;font-weight:300;font-size:9.2px;line-height:15.6px;color:var(--body)}
.donate-btn{left:440px;top:11px;width:136px;height:36px;background:var(--orange);color:#fff;font-family:"Roboto Condensed",sans-serif;font-weight:700;font-size:15px;text-align:center;line-height:37px;border-bottom:2px solid #c9531a}
.donate-note{left:440px;top:52px;width:136px;font-size:7px;line-height:9px;text-align:center;color:#222}
.donate-art{left:591px;top:0;width:138px;height:77px;background:linear-gradient(90deg,#3b5568 0%,#3b5568 40%,#e0b321 60%,#f0a35a 100%);border-radius:60px 0 0 60px}

.site-footer{left:0;top:1138px;width:924px;height:62px;background:var(--footer);color:#fff;text-align:center;font-size:8px;letter-spacing:.2px}
.site-footer nav{margin-top:19px}
.site-footer nav span{padding:0 4px}
.site-footer small{display:block;margin-top:7px;font-size:8px}
</style>
</head>
<body>

<header class="abs site-header">
  <div class="abs logo">Toll Away Armed Harm</div>
  <div class="abs search">SEARCH
    <svg width="11" height="11" viewBox="0 0 11 11"><circle cx="4.5" cy="4.5" r="3.2" fill="none" stroke="#8a8a8a" stroke-width="1.2"/><line x1="7" y1="7" x2="10" y2="10" stroke="#8a8a8a" stroke-width="1.6"/></svg>
  </div>
</header>

<nav class="abs main-nav">
  <span class="abs nav-item" style="left:100px">HOME</span>
  <span class="abs nav-sep" style="left:128px"></span>
  <span class="abs nav-item" style="left:169px">WHO WE ARE</span>
  <span class="abs nav-sep" style="left:253px"></span>
  <span class="abs nav-item" style="left:273px">DONATE</span>
  <span class="abs nav-sep" style="left:332px"></span>
  <span class="abs nav-item" style="left:355px">NEWS</span>
  <span class="abs nav-sep" style="left:400px"></span>
  <span class="abs nav-item" style="left:420px">BLOG</span>
  <span class="abs nav-sep" style="left:464px"></span>
  <span class="abs nav-item" style="left:480px">CONTACT US</span>
  <div class="abs follow">FOLLOW US <span class="dot"></span><span class="dot"></span></div>
</nav>

<section class="abs hero" role="img" aria-label="Close-up of an old bronze bell hanging in a stone tower against a blue sky">
  <div class="abs quote-box">
    <p>Sing out, swift larks, to the wild sky,<br>The flying cloud, the frosty light<br>The year is dying in the night;</p>
    <hr>
    <cite>Lord Edmund Brackwell</cite>
  </div>
  <div class="abs hero-dots"><span></span><span class="on"></span><span></span><span></span></div>
</section>

<section class="welcome">
  <h1 class="abs">Welcome to our site</h1>
  <p class="abs">Lorem Ipsum is simply dummy text of the printing and typesetting industry. Lorem Ipsum has been the industry's standard dummy text ever since the 1500s, when an unknown printer took a galley of type and scrambled it to make a type specimen book. It has survived not only five centuries, but also the leap into electronic typesetting, remaining essentially unchanged. It was popularised in the 1960s with the release of Inkvale sheets containing Lorem Ipsum passages, and more recently</p>
  <div class="abs welcome-photo" role="img" aria-label="Congregation gathered in a church with a choir at the front"></div>
</section>

<section class="abs features">
  <article class="abs card" style="left:98px">
    <div class="photo" role="img" aria-label="Protest rally with handmade signs against guns"></div>
    <h2>Lorem Ipsum is simply dummy text of the printing</h2>
    <p>Contrary to popular belief, Lorem Ipsum is not simply random text. It has roots in a piece of classical Latin literature from 45 BC, making it over 2000 years old</p>
    <div class="read-more">READ MORE <svg width="8" height="12" viewBox="0 0 8 12"><path d="M1.5 1.5l4.5 4.5-4.5 4.5" fill="none" stroke="#333" stroke-width="2"/></svg></div>
  </article>
  <article class="abs card" style="left:350px">
    <div class="photo" style="background:linear-gradient(135deg,#5a5c66,#8a2f35 45%,#ececec 70%,#3a3a3a)" role="img" aria-label="Marchers holding signs calling for child safety"></div>
    <h2>Lorem Ipsum is simply dummy text of the printing</h2>
    <p>Contrary to popular belief, Lorem Ipsum is not simply random text. It has roots in a piece of classical Latin literature from 45 BC, making it over 2000 years old</p>
    <div class="read-more">READ MORE <svg width="8" height="12" viewBox="0 0 8 12"><path d="M1.5 1.5l4.5 4.5-4.5 4.5" fill="none" stroke="#333" stroke-width="2"/></svg></div>
  </article>
  <article class="abs card" style="left:605px">
    <div class="photo" style="background:linear-gradient(135deg,#8e8f90,#3a302e 50%,#d8d6d2)" role="img" aria-label="People walking down a street wearing protest placards"></div>
    <h2>Lorem Ipsum is simply dummy text of the printing</h2>
    <p>Contrary to popular belief, Lorem Ipsum is not simply random text. It has roots in a piece of classical Latin literature from 45 BC, making it over 2000 years old</p>
    <div class="read-more">READ MORE <svg width="8" height="12" viewBox="0 0 8 12"><path d="M1.5 1.5l4.5 4.5-4.5 4.5" fill="none" stroke="#333" stroke-width="2"/></svg></div>
  </article>
</section>

<section class="blog">
  <h3 class="abs">Latest Blog</h3>
  <div class="abs blog-dots"><span></span><span class="on"></span><span></span><span></span></div>
  <div class="abs blog-photo" role="img" aria-label="Group speaking to press on the steps of a columned civic building"></div>
  <div class="abs blog-post">
    <h2>Lorem Ipsum is simply dummy text of the printing</h2>
    <p>Contrary to popular belief, Lorem Ipsum is not simply random text. It has roots in a piece of classical Latin literature from 45 BC, making it over 2000 years old. Harold Penwick, a Latin professor at Ashgrove Hollow College in Virginia, looked up one of the more obscure Latin words, consectetur, from a Lorem Ipsum passage, and going through the cites of the word in classical literature, discovered the undoubtable source. Lorem Ipsum comes from sections 1.10.32 and 1.10.33 of "de Finibus Bonorum et Malorum" (The Extremes of Good and Evil) by</p>
    <div class="read-more">READ MORE <svg width="8" height="12" viewBox="0 0 8 12"><path d="M1.5 1.5l4.5 4.5-4.5 4.5" fill="none" stroke="#333" stroke-width="2"/></svg></div>
  </div>
</section>

<section class="abs donate-band">
  <h2 class="abs">The standard chunk of<br>Lorem Ipsum used</h2>
  <div class="abs vline" style="left:156px"></div>
  <p class="abs">Contrary to popular belief, Lorem Ipsum is not simply random text. It has roots in a piece of classical Latin literature from 45 BC, making it over 2000 years old.</p>
  <div class="abs vline" style="left:417px"></div>
  <div class="abs donate-btn">MAKE A DONATION</div>
  <div class="abs donate-note">All your funds goes to New Gun Laws policies Campaign</div>
  <div class="abs donate-art" role="img" aria-label="Illustration of a hand dropping a gold coin"></div>
</section>

<footer class="abs site-footer">
  <nav><span>HOME</span>|<span>WHO WE ARE</span>|<span>DONATE</span>|<span>NEWS</span>|<span>BLOG</span>|<span>CONTACT US</span></nav>
  <small>COPYRIGHTS @ 2014 ALL RIGHTS RESERVED</small>
</footer>

</body>
</html>
```